Premium Gold Vodka Label Design

English ------------------- We need a label for a Vodka Bottle. Its a sparkling premium vodka with gold inside. The design should look premium. We tried it on our selves but it looks horrible. Therefore we need your help. The current name is lumora K, but we are open for any better suggestion. We attached the selfmade design. The label will be printed on the bottle. We have other design jobs for you (logo, other sorts)! English ------------------------ We need a label for a vodka bottle. This is a premium vodka which is offset with gold. The design should look like this. We have tried so far and failed. That is why we need your support. The name is so far lumora K. If you have better suggestions we would be pleased about other suggestions / ideas. In the appendix the failed design is stored. The label is to be applied by screen printing. In the case of good work follow-up projects are guaranteed (logo, other varieties, etc)!
Updates

Project Deadline Extended
Reason: We need more time for the decision.

Target Market(s)

USA

Colors

Designer to choose colors to be used in the design.

Requirements
Must have
• English ------------------------ The needed text is on our selfmade label that is attached. English ------------------------ The required texts are stored in the attached design.
Nice to have
• English ------------------------ Transparent places are allowed because we want to print the label on the bottom. English ------------------------ As the label is applied by screen printing, transparent areas are also possible.

```html
<!DOCTYPE html>
<html lang="en">
<head>
<meta charset="utf-8">
<title>Lumora K Vodka Label</title>
<link rel="stylesheet" href="https://fonts.googleapis.com/css2?family=Oswald:wght@300;400;700&display=swap">
<style>
  :root {
    --label-black: #000000;
    --gold-light: #fbe68a;
    --gold-mid: #e2b63a;
    --gold-deep: #b07a1c;
    --gold-text: #e9c347;
    --ink: #0b0b0b;
  }
  html, body {
    margin: 0;
    padding: 0;
    width: 696px;
    height: 1200px;
    overflow: hidden;
    background: var(--label-black);
  }
  .label {
    display: block;
    width: 696px;
    height: 1200px;
    background: var(--label-black);
  }
  .label-text {
    font-family: 'Oswald', sans-serif;
    fill: var(--gold-text);
    text-anchor: middle;
  }
  .arc-tagline { font-size: 24px; font-weight: 400; letter-spacing: 1.5px; }
  .karat { font-size: 36px; font-weight: 400; }
  .brand-name { font-size: 80px; font-weight: 700; fill: var(--ink); letter-spacing: 1px; }
  .product-type { font-size: 66px; font-weight: 700; fill: url(#gold-vertical); letter-spacing: 2px; }
  .detail-line { font-size: 33px; font-weight: 300; }
  .detail-line .accent { font-weight: 700; }
  .spec-line { font-size: 25px; font-weight: 400; }
  .frame-line { fill: none; stroke: url(#gold-diagonal); }
</style>
</head>
<body>
<svg class="label" viewBox="0 0 696 1200" xmlns="http://www.w3.org/2000/svg" role="img" aria-label="Lumora K premium gold sparkling vodka label">
  <defs>
    <linearGradient id="gold-diagonal" x1="0" y1="0" x2="1" y2="1">
      <stop offset="0" stop-color="var(--gold-light)"/>
      <stop offset="0.5" stop-color="var(--gold-mid)"/>
      <stop offset="1" stop-color="var(--gold-deep)"/>
    </linearGradient>
    <linearGradient id="gold-vertical" x1="0" y1="0" x2="0" y2="1">
      <stop offset="0" stop-color="var(--gold-light)"/>
      <stop offset="1" stop-color="var(--gold-deep)"/>
    </linearGradient>
    <linearGradient id="gold-ribbon" x1="0" y1="0" x2="1" y2="0">
      <stop offset="0" stop-color="var(--gold-deep)"/>
      <stop offset="0.3" stop-color="var(--gold-light)"/>
      <stop offset="0.7" stop-color="var(--gold-mid)"/>
      <stop offset="1" stop-color="var(--gold-deep)"/>
    </linearGradient>
    <radialGradient id="gold-soft">
      <stop offset="0" stop-color="var(--gold-light)"/>
      <stop offset="1" stop-color="var(--gold-deep)"/>
    </radialGradient>
    <path id="tagline-arc" d="M170,318 Q348,178 526,318"/>
  </defs>

  <g class="label-frame">
    <path class="frame-line" stroke-width="6"
      d="M112,960 L112,320 L140,320 L140,282 Q348,110 556,282 L556,320 L584,320 L584,960 L556,960 L556,1000 Q348,1095 140,1000 L140,960 Z"/>
    <path class="frame-line" stroke-width="2.5"
      d="M126,948 L126,334 L154,334 L154,290 Q348,130 542,290 L542,334 L570,334 L570,948 L542,948 L542,992 Q348,1075 154,992 L154,948 Z"/>
  </g>

  <text class="label-text arc-tagline">
    <textPath href="#tagline-arc" startOffset="50%">PREMIUM GOLD SPARKLING</textPath>
  </text>

  <g class="crest">
    <polygon class="frame-line" stroke-width="5" points="348,298 426,343 426,433 348,478 270,433 270,343"/>
    <polygon class="frame-line" stroke-width="2" points="348,312 414,350 414,426 348,464 282,426 282,350"/>
    <ellipse cx="348" cy="400" rx="54" ry="52" fill="url(#gold-soft)" role="img" aria-label="Crowned double-headed eagle emblem"/>
    <g class="crest-stars" fill="var(--gold-text)">
      <polygon points="304,342 306.5,349 314,349 308,353.5 310,360.5 304,356 298,360.5 300,353.5 294,349 301.5,349"/>
      <polygon points="392,342 394.5,349 402,349 396,353.5 398,360.5 392,356 386,360.5 388,353.5 382,349 389.5,349"/>
    </g>
  </g>

  <text class="label-text karat" x="184" y="398">24</text>
  <text class="label-text karat" x="514" y="398">KT</text>

  <ellipse cx="222" cy="470" rx="74" ry="22" fill="url(#gold-vertical)" role="img" aria-label="Gold scroll flourish, left"/>
  <ellipse cx="474" cy="470" rx="74" ry="22" fill="url(#gold-vertical)" role="img" aria-label="Gold scroll flourish, right"/>

  <g class="name-ribbon">
    <polygon points="14,610 86,560 86,660 40,650 62,625" fill="var(--gold-deep)"/>
    <polygon points="682,610 610,560 610,660 656,650 634,625" fill="var(--gold-deep)"/>
    <path d="M70,548 Q348,505 626,548 L626,656 Q348,615 70,656 Z" fill="url(#gold-ribbon)"/>
    <text class="label-text brand-name" x="348" y="634">LUMORA K</text>
  </g>

  <g class="divider" stroke="var(--gold-text)" stroke-width="2">
    <line x1="254" y1="672" x2="340" y2="672"/>
    <line x1="356" y1="672" x2="442" y2="672"/>
    <circle cx="348" cy="672" r="4" fill="var(--gold-text)" stroke="none"/>
  </g>

  <text class="label-text product-type" x="348" y="752">VODKA</text>

  <g class="divider" stroke="var(--gold-text)" stroke-width="2">
    <line x1="254" y1="780" x2="340" y2="780"/>
    <line x1="356" y1="780" x2="442" y2="780"/>
    <circle cx="348" cy="780" r="4" fill="var(--gold-text)" stroke="none"/>
  </g>

  <text class="label-text detail-line" x="348" y="840">DISTILLED <tspan class="accent">8</tspan> FILTERED</text>
  <text class="label-text detail-line" x="348" y="894">MADE IN GERMANY</text>

  <line x1="140" y1="918" x2="556" y2="918" stroke="var(--gold-text)" stroke-width="2"/>

  <text class="label-text spec-line" x="348" y="970">40% ALC VOL | 200 ML | 80 PROOF</text>

  <polygon class="footer-star" fill="var(--gold-text)"
    points="348,1008 350.5,1015 358,1015 352,1019.5 354,1026.5 348,1022 342,1026.5 344,1019.5 338,1015 345.5,1015"/>
</svg>
</body>
</html>
```